Creative Web design for Tattoo Artist

I am a tattoo artist with a private tattoo/art studio in Spring, TX. I need to design a website for my studio, to include the following "pages" :
-home/about
-FAQ
-Gallery
-Inquiries
-shop
We would like to see designs that are more dark or "moody", and like the colors black/gold.
I'd like my website to reflect my studio, an award winning private, upscale custom only tattoo studio.

I've attached some examples of styles we liked.

Target Market(s)

adults ages 18-50, interested in tattoos, or fine art

Industry/Entity Type

Tattoos/Fine Art/Arts

Coding

Coded - Design and coding required

Number of Pages Required

5+ page

Colors

Designer to choose colors to be used in the design.

Requirements
Must have
• gallery section, and e-commerce page set up so I can begin selling merchandise, I'd like the fonts to flow with my logo design

```html
<!DOCTYPE html>
<html lang="en">
<head>
<meta charset="utf-8">
<title>The Gilded Viper — Custom Tattoo Studio</title>
<link href="https://fonts.googleapis.com/css2?family=Prata&family=Roboto:wght@400;500;700&display=swap" rel="stylesheet">
<style>
:root{
  --gold:#ae9142;
  --gold-light:#c3a552;
  --black:#000;
  --panel:#0e0e0e;
  --panel-2:#161616;
  --line:#2a2a2a;
  --text:#e6e6e6;
  --muted:#cfcfcf;
  --photo-a:#3a3a3a;
  --photo-b:#111;
}
*{margin:0;padding:0;box-sizing:border-box}
html,body{width:1200px;height:4622px;overflow:hidden;background:var(--black)}
body{position:relative;font-family:"Roboto",Arial,sans-serif;color:var(--text)}
.abs{position:absolute}
.serif{font-family:"Prata",Georgia,serif;font-weight:400}
.photo{background:linear-gradient(135deg,var(--photo-a),var(--photo-b))}

/* header */
.hero-photo{left:0;top:0;width:1200px;height:790px;background:radial-gradient(ellipse at 65% 40%,#4a4a4a,#1a1a1a 60%,#0a0a0a)}
.topbar{left:0;top:0;width:1200px;height:129px;background:rgba(8,8,6,.78);border-top:2px solid var(--gold)}
.brand{left:140px;top:38px;width:130px;text-align:center;font-family:"Prata",Georgia,serif;color:var(--gold);font-size:17px;line-height:24px;letter-spacing:2px}
.util{top:30px;height:34px;display:flex;align-items:center;gap:10px;font-size:14px;font-weight:700;color:#fff;white-space:nowrap}
.icon-dot{width:32px;height:32px;border-radius:50%;background:var(--gold);display:flex;align-items:center;justify-content:center}
.btn-login{left:951px;top:24px;width:136px;height:40px;border-radius:20px;background:var(--gold);color:#fff;font-weight:700;font-size:15px;display:flex;align-items:center;justify-content:center;gap:10px}
.nav{top:86px;left:391px;display:flex;align-items:center;font-size:15px;color:#fff;letter-spacing:.3px}
.nav span{display:inline-block}
.nav .sep{margin:0 38px}
.nav .active{color:var(--gold)}

.hero-kicker{left:109px;top:316px;font-size:21px;color:var(--gold)}
.hero-title{left:109px;top:358px;font-size:42px;line-height:48px;color:#fff}
.btn{height:40px;border-radius:20px;background:var(--gold);color:#fff;font-size:14px;font-weight:700;display:flex;align-items:center;justify-content:center;gap:10px;letter-spacing:.3px}

.sec-title{font-size:33px;color:#fff;display:flex;align-items:center;gap:10px;white-space:nowrap}
.sec-title em{font-style:normal;color:var(--gold)}
.star{width:24px;height:24px}
.para{font-size:15px;line-height:25.7px;color:var(--muted);text-align:justify}

/* shop */
.card{width:228px;height:316px;background:var(--panel);border:1px solid #1c1c1c;border-radius:4px}
.card .thumb{position:absolute;left:8px;top:7px;width:212px;height:148px;background:radial-gradient(circle at 50% 50%,#202020,#070707);border-radius:2px}
.card .name{position:absolute;left:28px;top:180px;font-size:14px;color:#fff;font-family:"Prata",Georgia,serif}
.card .price{position:absolute;left:28px;top:212px;font-size:14px;color:var(--gold)}
.card .desc{position:absolute;left:28px;top:243px;font-size:13.5px;color:#ddd}
.card .buy{position:absolute;left:28px;top:274px;font-size:13.5px;font-weight:700;color:var(--gold);display:flex;gap:8px;align-items:center}

/* faq */
.faq{width:470px;height:56px;border:2px solid #3b3b3b;border-radius:28px;background:#0a0a0a;display:flex;align-items:center;justify-content:space-between;padding:0 18px 0 24px;font-size:16.5px;font-weight:700;color:#fff}
.faq.open{background:var(--gold);border-color:var(--gold);color:#f5e7bd}
.faq .chev{width:24px;height:24px;border-radius:50%;background:#fff;display:flex;align-items:center;justify-content:center}
.faq.open .chev{background:#f3e3b4}

.gal{width:314px;height:213px}

/* footer */
.foot-h{font-size:14px;font-weight:700;color:#fff}
.foot-h::after{content:"";display:block;width:28px;height:2px;background:#fff;margin-top:10px}
.foot-list{list-style:none;font-size:14px;color:#fff}
.foot-list li{height:30.7px;display:flex;align-items:center;gap:14px}
.foot-list li::before{content:"»";font-size:15px}
.vline{width:1px;background:#333}
.social{width:32px;height:32px;border-radius:50%;background:var(--gold)}
.contact-row{display:flex;align-items:center;gap:18px;font-size:14px;color:#fff;line-height:19px}
.c-ring{width:32px;height:32px;border-radius:50%;border:1.5px solid #fff;display:flex;align-items:center;justify-content:center;flex:none}
</style>
</head>
<body>

<!-- HERO -->
<div class="abs hero-photo" role="img" aria-label="Black and white photo of a tattoo artist inking a seated client's arm"></div>
<svg class="abs" style="left:0;top:600px" width="1200" height="200" viewBox="0 0 1200 200">
  <path d="M0,75 C150,20 240,120 440,162 C650,205 920,130 1200,80 L1200,200 L0,200 Z" fill="#000"/>
  <path d="M0,20 C150,-8 240,105 440,140 C650,178 920,110 1200,70 L1200,82 C920,140 650,212 440,168 C240,128 150,30 0,85 Z" fill="var(--gold)"/>
</svg>

<div class="abs topbar"></div>
<div class="abs brand">THE<br>GILDED<br>VIPER</div>

<div class="abs util" style="left:664px">
  <span class="icon-dot"><svg width="15" height="15" viewBox="0 0 24 24" fill="#fff"><path d="M2 3h3l3 11h11l3-8H7"/><circle cx="9" cy="19" r="2"/><circle cx="18" cy="19" r="2"/></svg></span>Cart
</div>
<div class="abs util" style="left:764px">
  <span class="icon-dot"><svg width="14" height="14" viewBox="0 0 24 24" fill="#fff"><path d="M6.6 10.8a15 15 0 0 0 6.6 6.6l2.2-2.2c.3-.3.7-.4 1-.2 1.1.4 2.3.6 3.6.6.6 0 1 .4 1 1V20c0 .6-.4 1-1 1A17 17 0 0 1 3 4c0-.6.4-1 1-1h3.5c.6 0 1 .4 1 1 0 1.3.2 2.5.6 3.6.1.3 0 .7-.2 1z"/></svg></span>+1 555 014 2277
</div>
<div class="abs btn-login">LOGIN <svg width="12" height="14" viewBox="0 0 12 14" fill="#fff"><rect x="1" y="6" width="10" height="8" rx="1"/><path d="M3 6V4a3 3 0 0 1 6 0v2" stroke="#fff" stroke-width="1.6" fill="none"/></svg></div>

<div class="abs nav">
  <span class="active">HOME</span><span class="sep">|</span><span>ABOUT</span><span class="sep">|</span><span>FAQ</span><span class="sep">|</span><span>GALLERY</span><span class="sep">|</span><span>INQUIRIES</span><span class="sep">|</span><span>SHOP</span>
</div>

<div class="abs serif hero-kicker">WELCOME TO</div>
<div class="abs serif hero-title">THE GILDED<br>VIPER</div>
<div class="abs btn" style="left:109px;top:481px;width:173px">GET STARTED
  <svg width="14" height="14" viewBox="0 0 14 14"><circle cx="7" cy="7" r="7" fill="#fff"/><path d="M5 4l3 3-3 3" stroke="#ae9142" stroke-width="1.8" fill="none"/></svg></div>

<!-- ABOUT -->
<svg class="abs" style="left:134px;top:898px" width="396" height="396"><circle cx="198" cy="198" r="196" fill="none" stroke="var(--gold)" stroke-width="2"/></svg>
<div class="abs photo" style="left:140px;top:904px;width:384px;height:384px;border-radius:50%" role="img" aria-label="Close-up of a tattoo artist at work"></div>

<div class="abs serif sec-title" style="left:588px;top:902px">
  <svg class="star" viewBox="0 0 24 24"><path d="M12 0l3 9 9 3-9 3-3 9-3-9-9-3 9-3z" fill="var(--gold)"/></svg>ABOUT <em>US</em></div>
<p class="abs para" style="left:588px;top:960px;width:479px">Lorem ipsum dolor sit ameted consectetur adipiscing elited sed do eiusmod tempor incididunt ut labore et dolore magna aliqua Ut enim ad minim veniamed quis nostrud exercitation ullamco laboris nisi ut aliquip commodo consequat Duis aute irure dolor in reprehenderit in voluptate velit esse cillum dolore eu fugiat nulla pariatur Excepteur sint occaecat cupidatat non proident, sunt in culpa qui officia deserunt mollit anim id est laborum Lorem ipsum dolor sit amet, consectetur adipiscing elit, sed do eiusmod tempor incididunt ut labore et dolore magna aliqua. Ut enim ad minim veniam, quis nostrud exercitation ullamco laboris nisi ut aliquip ex ea commodog.</p>
<div class="abs btn" style="left:588px;top:1249px;width:171px">LEARN MORE
  <svg width="14" height="14" viewBox="0 0 14 14"><circle cx="7" cy="7" r="7" fill="#fff"/><path d="M5 4l3 3-3 3" stroke="#ae9142" stroke-width="1.8" fill="none"/></svg></div>

<!-- SHOP -->
<div class="abs serif sec-title" style="left:0;width:1200px;justify-content:center;top:1392px">
  <svg class="star" viewBox="0 0 24 24"><path d="M12 0l3 9 9 3-9 3-3 9-3-9-9-3 9-3z" fill="var(--gold)"/></svg>OUR <em>SHOP</em></div>

<div class="abs card" style="left:111px;top:1482px"><div class="thumb" role="img" aria-label="Black t-shirt with gold studio mark"></div><div class="name">T SHIRTS</div><div class="price">$39.00</div><div class="desc">Lorem ipsum dolored sited</div><div class="buy">BUY NOW <svg width="14" height="12" viewBox="0 0 24 20" fill="var(--gold)"><path d="M1 1h4l3 11h12l3-8H7"/><circle cx="9" cy="17" r="2"/><circle cx="18" cy="17" r="2"/></svg></div></div>
<div class="abs card" style="left:361px;top:1482px"><div class="thumb" role="img" aria-label="Black mug with gold studio mark"></div><div class="name">CUPS</div><div class="price">$39.00</div><div class="desc">Lorem ipsum dolored sited</div><div class="buy">BUY NOW <svg width="14" height="12" viewBox="0 0 24 20" fill="var(--gold)"><path d="M1 1h4l3 11h12l3-8H7"/><circle cx="9" cy="17" r="2"/><circle cx="18" cy="17" r="2"/></svg></div></div>
<div class="abs card" style="left:612px;top:1482px"><div class="thumb" role="img" aria-label="Black cap with gold studio mark"></div><div class="name">CAP</div><div class="price">$39.00</div><div class="desc">Lorem ipsum dolored sited</div><div class="buy">BUY NOW <svg width="14" height="12" viewBox="0 0 24 20" fill="var(--gold)"><path d="M1 1h4l3 11h12l3-8H7"/><circle cx="9" cy="17" r="2"/><circle cx="18" cy="17" r="2"/></svg></div></div>
<div class="abs card" style="left:861px;top:1482px"><div class="thumb" role="img" aria-label="Black tote bag with gold studio mark"></div><div class="name">T SHIRTS</div><div class="price">$39.00</div><div class="desc">Lorem ipsum dolored sited</div><div class="buy">BUY NOW <svg width="14" height="12" viewBox="0 0 24 20" fill="var(--gold)"><path d="M1 1h4l3 11h12l3-8H7"/><circle cx="9" cy="17" r="2"/><circle cx="18" cy="17" r="2"/></svg></div></div>

<!-- CONTACT -->
<div class="abs serif sec-title" style="left:115px;top:1910px">
  <svg class="star" viewBox="0 0 24 24"><path d="M12 0l3 9 9 3-9 3-3 9-3-9-9-3 9-3z" fill="var(--gold)"/></svg>CONTACT <em>US</em></div>
<p class="abs para" style="left:115px;top:1970px;width:477px">Lorem ipsum dolor sit ameted consectetur adipiscing elited sed do eiusmod tempor incididunt ut labore et dolore magna aliqua Ut enim ad minim veniamed quis nostrud exercitation ullamco laboris nisi ut aliquip commodo consequat Duis aute irure dolor in reprehenderit in voluptate velit esse cillum dolore eu fugiat nulla pariatur Excepteur sint occaecat cupidatat non proident, sunt in culpa qui officia deserunt mollit anim id est laborum Lorem ipsum dolor sit amet, consectetur adipiscing elit, sed do eiusmod tempor incididunt ut labore et dolore magna aliqua. Ut enim ad minim veniam, quis nostrud exercitation ullamco laboris nisi ut aliquip ex ea commodog.</p>
<div class="abs btn" style="left:115px;top:2257px;width:171px">LEARN MORE
  <svg width="14" height="14" viewBox="0 0 14 14"><circle cx="7" cy="7" r="7" fill="#fff"/><path d="M5 4l3 3-3 3" stroke="#ae9142" stroke-width="1.8" fill="none"/></svg></div>
<div class="abs photo" style="left:648px;top:1884px;width:274px;height:306px" role="img" aria-label="Tattoo machine and ink bottles on a workbench"></div>
<div class="abs" style="left:779px;top:2000px;width:308px;height:332px;background:linear-gradient(135deg,#cfcfcf,#4a4a4a)" role="img" aria-label="Gloved hands tattooing a detailed design"></div>

<!-- FAQ -->
<div class="abs serif sec-title" style="left:0;width:1200px;justify-content:center;top:2411px">
  <svg class="star" viewBox="0 0 24 24"><path d="M12 0l3 9 9 3-9 3-3 9-3-9-9-3 9-3z" fill="var(--gold)"/></svg>FREQUENTLY ASKED <em>QUESTIONS</em></div>

<div class="abs faq" style="left:117px;top:2490px">Lorem ipsum dolor consectetur adipiscing<span class="chev"><svg width="10" height="10" viewBox="0 0 10 10"><path d="M3 1l4 4-4 4" stroke="#000" stroke-width="2" fill="none"/></svg></span></div>
<div class="abs faq" style="left:614px;top:2490px">Lorem ipsum dolor consectetur adipiscing<span class="chev"><svg width="10" height="10" viewBox="0 0 10 10"><path d="M3 1l4 4-4 4" stroke="#000" stroke-width="2" fill="none"/></svg></span></div>
<div class="abs faq" style="left:117px;top:2568px">Lorem ipsum dolor consectetur adipiscing<span class="chev"><svg width="10" height="10" viewBox="0 0 10 10"><path d="M3 1l4 4-4 4" stroke="#000" stroke-width="2" fill="none"/></svg></span></div>
<div class="abs faq" style="left:614px;top:2568px">Lorem ipsum dolor consectetur adipiscing<span class="chev"><svg width="10" height="10" viewBox="0 0 10 10"><path d="M3 1l4 4-4 4" stroke="#000" stroke-width="2" fill="none"/></svg></span></div>
<div class="abs faq" style="left:117px;top:2646px">Lorem ipsum dolor consectetur adipiscing<span class="chev"><svg width="10" height="10" viewBox="0 0 10 10"><path d="M3 1l4 4-4 4" stroke="#000" stroke-width="2" fill="none"/></svg></span></div>
<div class="abs faq open" style="left:614px;top:2646px">Lorem ipsum dolor consectetur adipiscing<span class="chev"><svg width="10" height="10" viewBox="0 0 10 10"><path d="M3 1l4 4-4 4" stroke="#ae9142" stroke-width="2" fill="none"/></svg></span></div>
<div class="abs faq" style="left:117px;top:2724px">Lorem ipsum dolor consectetur adipiscing<span class="chev"><svg width="10" height="10" viewBox="0 0 10 10"><path d="M3 1l4 4-4 4" stroke="#000" stroke-width="2" fill="none"/></svg></span></div>
<div class="abs faq" style="left:614px;top:2724px">Lorem ipsum dolor consectetur adipiscing<span class="chev"><svg width="10" height="10" viewBox="0 0 10 10"><path d="M3 1l4 4-4 4" stroke="#000" stroke-width="2" fill="none"/></svg></span></div>

<!-- CUSTOM TATTOO -->
<div class="abs" style="left:8px;top:2856px;width:532px;height:448px;border:2px solid var(--gold)"></div>
<div class="abs photo" style="left:0;top:2866px;width:530px;height:436px" role="img" aria-label="Tattoo artist working on a client's arm in a patterned studio"></div>
<div class="abs serif sec-title" style="left:613px;top:2888px">
  <svg class="star" viewBox="0 0 24 24"><path d="M12 0l3 9 9 3-9 3-3 9-3-9-9-3 9-3z" fill="var(--gold)"/></svg>CUSTOM <em>&nbsp;TATTOO</em></div>
<p class="abs para" style="left:613px;top:2948px;width:476px">Lorem ipsum dolor sit ameted consectetur adipiscing elited sed do eiusmod tempor incididunt ut labore et dolore magna aliqua Ut enim ad minim veniamed quis nostrud exercitation ullamco laboris nisi ut aliquip commodo consequat Duis aute irure dolor in reprehenderit in voluptate velit esse cillum dolore eu fugiat nulla pariatur Excepteur sint occaecat cupidatat non proident, sunt in culpa qui officia deserunt mollit anim id est laborum Lorem ipsum dolor sit amet, consectetur adipiscing elit, sed do eiusmod tempor incididunt ut labore et dolore magna aliqua. Ut enim ad minim veniam, quis nostrud exercitation ullamco laboris nisi ut aliquip ex ea commodog.</p>
<div class="abs btn" style="left:613px;top:3235px;width:171px">LEARN MORE
  <svg width="14" height="14" viewBox="0 0 14 14"><circle cx="7" cy="7" r="7" fill="#fff"/><path d="M5 4l3 3-3 3" stroke="#ae9142" stroke-width="1.8" fill="none"/></svg></div>

<!-- GALLERY -->
<div class="abs serif sec-title" style="left:0;width:1200px;justify-content:center;top:3387px">
  <svg class="star" viewBox="0 0 24 24"><path d="M12 0l3 9 9 3-9 3-3 9-3-9-9-3 9-3z" fill="var(--gold)"/></svg>OUR <em>GALLERY</em></div>
<div class="abs gal" style="left:115px;top:3468px;background:linear-gradient(135deg,#d8d8d8,#5a5a5a)" role="img" aria-label="Fine-line mandala tattoo in progress on a forearm"></div>
<div class="abs gal" style="left:443px;top:3468px;background:linear-gradient(135deg,#6a6a6a,#1e1e1e)" role="img" aria-label="Studio interior with lighting equipment"></div>
<div class="abs gal" style="left:773px;top:3468px;background:linear-gradient(135deg,#9a9a9a,#2a2a2a)" role="img" aria-label="Artist tattooing a large back piece"></div>
<div class="abs gal" style="left:115px;top:3699px;background:linear-gradient(135deg,#7a7a7a,#151515)" role="img" aria-label="Desk setup with monitors and microphone"></div>
<div class="abs gal" style="left:443px;top:3699px;background:radial-gradient(ellipse at 50% 40%,#8a8a8a,#0d0d0d 70%)" role="img" aria-label="Tattooed back of a person with arms raised"></div>
<div class="abs gal" style="left:773px;top:3699px;background:linear-gradient(135deg,#bdbdbd,#4e4e4e)" role="img" aria-label="Gloved hands wiping a fresh tattoo"></div>

<!-- FOOTER WAVE -->
<svg class="abs" style="left:0;top:4050px" width="1200" height="170" viewBox="0 0 1200 170">
  <path d="M0,150 C180,70 380,30 620,28 C860,28 1060,60 1200,130 L1200,160 C1050,95 880,62 640,55 C400,52 200,90 0,160 Z" fill="var(--gold)"/>
</svg>

<!-- FOOTER -->
<div class="abs serif" style="left:120px;top:4320px;width:140px;text-align:center;color:var(--gold);font-size:17px;line-height:24px;letter-spacing:2px">THE<br>GILDED<br>VIPER</div>
<div class="abs social" style="left:113px;top:4457px"></div>
<div class="abs social" style="left:151px;top:4457px"></div>
<div class="abs social" style="left:190px;top:4457px"></div>
<div class="abs social" style="left:228px;top:4457px"></div>

<div class="abs vline" style="left:323px;top:4270px;height:225px"></div>
<div class="abs vline" style="left:556px;top:4270px;height:225px"></div>
<div class="abs vline" style="left:874px;top:4270px;height:225px"></div>

<div class="abs foot-h" style="left:404px;top:4270px">QUICK LINKS</div>
<ul class="abs foot-list" style="left:404px;top:4313px">
  <li>Home</li><li>About</li><li>FAQ</li><li>Gallery</li><li>Inquiries</li><li>Shop</li>
</ul>

<div class="abs foot-h" style="left:615px;top:4270px">CONTACT US</div>
<div class="abs contact-row" style="left:615px;top:4322px">
  <span class="c-ring"><svg width="12" height="14" viewBox="0 0 12 16" fill="#fff"><path d="M6 0a6 6 0 0 0-6 6c0 4.5 6 10 6 10s6-5.5 6-10a6 6 0 0 0-6-6zm0 8.5A2.5 2.5 0 1 1 6 3.5a2.5 2.5 0 0 1 0 5z"/></svg></span>
  <span>Lorem ipsum dolor sit<br>consectetur adipiscing</span></div>
<div class="abs contact-row" style="left:615px;top:4381px;font-weight:700">
  <span class="c-ring"><svg width="13" height="13" viewBox="0 0 24 24" fill="#fff"><path d="M6.6 10.8a15 15 0 0 0 6.6 6.6l2.2-2.2c.3-.3.7-.4 1-.2 1.1.4 2.3.6 3.6.6.6 0 1 .4 1 1V20c0 .6-.4 1-1 1A17 17 0 0 1 3 4c0-.6.4-1 1-1h3.5c.6 0 1 .4 1 1 0 1.3.2 2.5.6 3.6.1.3 0 .7-.2 1z"/></svg></span>
  <span>+1 555 014 2277</span></div>
<div class="abs contact-row" style="left:615px;top:4439px">
  <span class="c-ring"><svg width="14" height="11" viewBox="0 0 16 12"><rect x="0.5" y="0.5" width="15" height="11" fill="#fff"/><path d="M1 1l7 6 7-6" stroke="#000" stroke-width="1.4" fill="none"/></svg></span>
  <span>info@gildedviper-studio.com</span></div>

<div class="abs foot-h" style="left:933px;top:4270px">OTHER LINKS</div>
<ul class="abs foot-list" style="left:933px;top:4313px">
  <li>Careers</li><li>Our Partners</li><li>Terms &amp; Conditions</li><li>Privacy Ploicy</li><li>FAQ</li>
</ul>

<div class="abs" style="left:100px;top:4544px;width:1000px;height:1px;background:#2e2e2e"></div>
<div class="abs" style="left:0;top:4568px;width:1200px;text-align:center;font-size:14px;color:#fff">© 2023 &nbsp;The Gilded Viper . All Rights Reserved</div>

</body>
</html>
```